Design for Torvik Ginger Chewy Candy!

Hello! We are Torvik Enterprises Corp, a food manufacturer and distributor based in Los Angeles, CA. We manufacture Chips, Cookies, Juices, Dairy, and last but not least, Candies! We are launching our Ginger Chewy Candy soon and we need a great design for it!

Our Ginger Chewy Candy is a perfect mixture between sweet and spicy from the ginger itself. Torvik Ginger Chewy Candy a good relief for sore throat and nausea.

Now, other than a great design, we also welcome brand suggestions for the candy.
If you can come up with a logo for the Ginger Candy, that would be swell!

We are open to unique and out of the box design. We chose a few color schemes for the design, but feel free to step out of the box if you feel it suits the brand.

We don't have the exact size for the plastic pouch, but it should be a generic small plastic pouch size (approximately 4 oz resealable plastic pouch)

Please have fun designing the project, we can't wait to see all the great designs!

Cheers!

Target Market(s)

USA and Asian market
Age 30-70
Male and Female

Industry/Entity Type

Manufacture

Font styles to use
Serif
Sans Serif
Decorative

Colors
fff3d1
fee18a
fece3e
fbc994
fce8d3

Requirements
Must have
• Torvik Logo
• A picture of ginger (illustrations or photographs are welcome)
Nice to have
• Coating suggestions like Matte surface or SPOT UV
• Give us ideas of what the name of the chewy candy should be. Product name ideas are welcome!

```html
<!DOCTYPE html>
<html lang="en">
<head>
<meta charset="utf-8">
<title>Torvik Ginger Candy Pouch</title>
<link rel="stylesheet" href="https://fonts.googleapis.com/css2?family=Nunito:wght@600&family=Yellowtail&display=block">
<style>
  :root {
    --canvas: #ffffff;
    --cream: #fff3d1;
    --butter: #fee18a;
    --sun: #fece3e;
    --amber: #f6a93a;
    --deep-amber: #f39a1f;
    --pale-gold: #f3d27a;
    --white: #ffffff;
    --navy: #2b3a8f;
    --sky-blue: #1f80c4;
    --ginger-skin: #e9c79a;
    --ginger-flesh: #f6df7c;
  }
  * { margin: 0; padding: 0; box-sizing: border-box; }
  html, body { width: 960px; height: 1200px; overflow: hidden; background: var(--canvas); }
  .canvas { position: relative; width: 960px; height: 1200px; }
  .pouch-art { position: absolute; inset: 0; }
  .brand-name {
    position: absolute; left: 530px; top: 400px; width: 170px;
    text-align: center;
    font-family: "Nunito", sans-serif; font-weight: 600;
    font-size: 44px; color: var(--navy); letter-spacing: -0.5px;
  }
  .tagline {
    position: absolute; left: 520px; top: 548px; width: 210px;
    text-align: right;
    font-family: "Nunito", sans-serif; font-weight: 600;
    font-size: 15.5px; line-height: 1.35; color: var(--sky-blue);
  }
  .product-title {
    position: absolute; margin: 0;
    font-family: "Yellowtail", cursive; font-weight: 400; font-style: normal;
    line-height: 1; white-space: nowrap;
    text-shadow: 1px 3px 4px rgba(150, 90, 0, 0.25);
    transform-origin: left center;
  }
  .product-title.first { left: 318px; top: 712px; font-size: 132px; color: var(--deep-amber); transform: rotate(-6deg); }
  .product-title.second { left: 418px; top: 808px; font-size: 124px; color: var(--pale-gold); transform: rotate(-6deg); }
  .net-weight {
    position: absolute; left: 338px; top: 920px;
    font-family: "Nunito", sans-serif; font-weight: 600;
    font-size: 20px; color: var(--sky-blue);
  }
</style>
</head>
<body>
<div class="canvas">
  <svg class="pouch-art" width="960" height="1200" viewBox="0 0 960 1200">
    <defs>
      <clipPath id="pouch-shape">
        <rect x="190" y="205" width="580" height="800"/>
      </clipPath>
      <linearGradient id="pouch-ground" x1="0" y1="0" x2="0.3" y2="1">
        <stop offset="0" stop-color="#fbe4ad"/>
        <stop offset="0.45" stop-color="#fbd683"/>
        <stop offset="0.75" stop-color="#f6a93a"/>
        <stop offset="1" stop-color="#f9c66a"/>
      </linearGradient>
      <radialGradient id="ginger-tones" cx="0.5" cy="0.5" r="0.6">
        <stop offset="0" stop-color="#f6df7c"/>
        <stop offset="0.6" stop-color="#e9c79a"/>
        <stop offset="1" stop-color="#e9c79a" stop-opacity="0"/>
      </radialGradient>
    </defs>
    <g clip-path="url(#pouch-shape)">
      <rect class="pouch-panel" x="190" y="205" width="580" height="800" fill="url(#pouch-ground)"/>
      <path class="top-window" d="M430,195 L780,195 L780,428 C700,462 600,490 520,488 C460,478 424,400 430,195 Z" fill="var(--white)"/>
      <path class="accent-swoop" d="M380,742 C500,680 650,590 780,492 L780,470 C650,566 500,660 372,726 Z" fill="var(--amber)"/>
      <path class="lower-stripe" d="M262,1015 C232,900 250,784 360,726 C490,660 650,566 780,480 L780,520 C650,606 506,690 384,748 C282,796 266,904 292,1015 Z" fill="var(--butter)"/>
      <path class="lower-window" d="M292,1015 C266,904 282,796 384,748 C506,690 650,606 780,520 L780,1015 Z" fill="var(--white)"/>
      <g role="img" aria-label="Illustration of a fresh ginger root with green leaves and sliced ginger pieces">
        <ellipse cx="372" cy="528" rx="112" ry="110" fill="url(#ginger-tones)"/>
      </g>
    </g>
  </svg>
  <div class="brand-name">Torvik</div>
  <p class="tagline">a good relief for sore<br>throat and nausea.</p>
  <h1 class="product-title first">Ginger</h1>
  <h2 class="product-title second">Candy</h2>
  <div class="net-weight">4oz</div>
</div>
</body>
</html>
```